Private Investment Firm Needs PowerPoint Presentation Template

Design PowerPoint template, take Pinebrook-submitted rough presentation draft, and drop it into new template. See attached Project Brief file for more detail.
Updates

Some decent designs have been submitted but they seem to lack the understanding of our target markets. I am hopeful that more time and feedback will result in better results.

Target Market(s)

Private company owners and intermediaries.

Font styles to use
Serif

Colors
3176b5

Requirements
Must have
• See attached Project Brief.
Nice to have
Should not have
• No B2C fluff--this is a B2B project.

```html
<!DOCTYPE html>
<html lang="en">
<head>
<meta charset="utf-8">
<title>Pinebrook Impact - By the Numbers</title>
<link rel="stylesheet" href="https://fonts.googleapis.com/css2?family=Montserrat:wght@400;500;600;700&family=Libre+Baskerville&display=swap">
<style>
  :root {
    --brand-blue: #0070c0;
    --title-blue: #1a6cbf;
    --ink-grey: #555555;
    --cell-grey: #d9d9d9;
    --head-light: #f3f3f3;
    --page-ink: #222222;
    --white: #ffffff;
  }
  * { margin: 0; padding: 0; box-sizing: border-box; }
  html, body { width: 1200px; height: 676px; overflow: hidden; background: var(--white); }
  .slide { position: relative; width: 1200px; height: 676px; overflow: hidden; background: var(--white); font-family: "Montserrat", sans-serif; }
  .side-rail { position: absolute; left: 0; top: 0; width: 44px; height: 676px; background: var(--brand-blue); }
  .side-rail-url {
    position: absolute; left: 22px; top: 336px;
    transform: translate(-50%, -50%) rotate(-90deg);
    font-family: "Libre Baskerville", serif; font-size: 13.5px; color: var(--white);
    white-space: nowrap; letter-spacing: 0.2px;
  }
  .edge-rail { position: absolute; right: 0; top: 0; width: 12px; height: 676px; background: var(--brand-blue); }
  .page-number { position: absolute; left: 1157px; top: 18px; font-family: "Libre Baskerville", serif; font-size: 17px; color: var(--page-ink); }
  .slide-title { position: absolute; left: 86px; top: 82px; font-size: 28px; font-weight: 700; color: var(--title-blue); letter-spacing: 0.3px; }
  .lead {
    position: absolute; right: 748px; top: 225px; text-align: right;
    font-size: 40px; line-height: 42px; font-weight: 600; letter-spacing: 0.5px;
  }
  .lead-accent { color: var(--brand-blue); display: block; }
  .lead-muted { color: var(--ink-grey); display: block; }
  .panel { position: absolute; left: 482px; top: 170px; width: 706px; height: 334px; background: var(--brand-blue); }
  .photo-band {
    position: absolute; left: 470px; top: 504px; width: 718px; height: 172px;
    background: linear-gradient(100deg, #ffffff 0%, #f1f3f4 35%, #d9e0e3 70%, #c3ccd0 100%);
  }
  .impact-table { position: absolute; left: 570px; top: 249px; font-size: 14px; }
  .cell { position: absolute; display: flex; align-items: center; }
  .head { background: var(--head-light); color: var(--brand-blue); font-weight: 600; line-height: 18px; top: 0; height: 53px; }
  .body { background: var(--cell-grey); color: var(--ink-grey); font-weight: 400; letter-spacing: 0.2px; }
  .col-a { left: 0; width: 258px; padding-left: 48px; }
  .col-b { left: 262px; width: 136px; justify-content: center; }
  .col-c { left: 402px; width: 137px; justify-content: center; }
  .head.col-a { padding-left: 48px; }
  .head.col-b, .head.col-c { justify-content: flex-start; padding-left: 35px; }
  .body.col-a { padding-left: 42px; }
  .row-1 { top: 65px; height: 35px; }
  .row-2 { top: 101px; height: 35px; }
  .row-3 { top: 139px; height: 34px; }
  .brand { position: absolute; left: 68px; top: 616px; display: flex; align-items: center; gap: 10px; }
  .brand-dot { width: 36px; height: 36px; border-radius: 50%; background: var(--brand-blue); }
  .brand-name { font-family: "Libre Baskerville", serif; font-size: 18px; color: var(--brand-blue); letter-spacing: 1px; }
</style>
</head>
<body>
<div class="slide">
  <div class="side-rail"><span class="side-rail-url">www.pinebrookcapital.com</span></div>
  <div class="edge-rail"></div>
  <div class="page-number">20</div>
  <h1 class="slide-title">PINEBROOK IMPACT - BY THE NUMBERS</h1>

  <p class="lead">
    <span class="lead-accent">During Pine-</span>
    <span class="lead-accent">brook’s average</span>
    <span class="lead-accent">investment term,</span>
    <span class="lead-muted">our impact has</span>
    <span class="lead-muted">been noteworthy</span>
  </p>

  <div class="panel"></div>
  <div class="photo-band" role="img" aria-label="Photo of white modern building facade with curved vertical fins"></div>

  <div class="impact-table">
    <div class="cell head col-a">IMPACT CATEGORY</div>
    <div class="cell head col-b">ACTUAL<br>IMPACT</div>
    <div class="cell head col-c">MIN/MAX*<br>REMOVED</div>

    <div class="cell body col-a row-1">Average Revenue Growth</div>
    <div class="cell body col-b row-1">113%</div>
    <div class="cell body col-c row-1">91%</div>

    <div class="cell body col-a row-2">Average EBITDA Growth</div>
    <div class="cell body col-b row-2">75%</div>
    <div class="cell body col-c row-2">78%</div>

    <div class="cell body col-a row-3">Average Employee Growth</div>
    <div class="cell body col-b row-3">213%</div>
    <div class="cell body col-c row-3">49%</div>
  </div>

  <div class="brand">
    <span class="brand-dot"></span>
    <span class="brand-name">PINEBROOK CAPITAL</span>
  </div>
</div>
</body>
</html>
```